Redesign This Psychology Website

We would like a slight redesign of this successful psychology (relationship counselling) website:

www.TheKelvaleClinic.com.au

We are updating the website, and we'd like a slight refresh of the design and style.

Please keep to very similar colours, and use the same logo. We're looking for around 10 page templates, however the main one is the home page.

Keep in mind, this website already converts quite well, so we want a new, fresh design in keeping with this one. Please don't bother designing something too extremely different.

thanks :)

Target Market(s)

couples who are looking for relationship counselling. Men and women, 25 - 70, across Australia

Industry/Entity Type

Psychology

Number of Pages Required

5+ page

Font styles to use
Sans Serif

Colors
87cfc6
b7a5cd
ec1f27
ffffff
cee9f5

Requirements
Must have
• a similar look to the current design, just looking for a slight refresh.
• Search bar
• Areas for lots of photos
• same logo
• lots of content areas
Nice to have
• great content areas, where we can display a lot of content and our areas.
Should not have
• no colors like orange, etc.
• should not have a totally different feel.

```html
<!DOCTYPE html>
<html lang="en">
<head>
<meta charset="utf-8">
<title>The Kelvale Clinic – Relationship Counselling</title>
<link href="https://fonts.googleapis.com/css2?family=Open+Sans:wght@400;600;700&display=swap" rel="stylesheet">
<style>
:root{
  --teal:#87cfc6;
  --teal-dark:#6cbfb4;
  --red:#ec1f27;
  --lilac:#b7a5cd;
  --sky:#cee9f5;
  --white:#ffffff;
  --grey-bg:#ececec;
  --ink:#333333;
  --muted:#666666;
  --line:#dddddd;
}
*{box-sizing:border-box;margin:0;padding:0}
html,body{width:1200px;height:4018px;overflow:hidden}
body{font-family:'Open Sans',sans-serif;color:var(--ink);background:var(--white);font-size:13px}
.wrap{width:940px;margin:0 auto;position:relative}
a{color:inherit;text-decoration:none}
.btn{display:inline-block;background:var(--teal-dark);color:var(--white);font-size:11px;font-weight:600;padding:6px 14px;text-transform:uppercase;letter-spacing:.3px;white-space:nowrap}
.section-title{color:var(--red);font-size:26px;font-weight:400;text-transform:uppercase}
.photo{display:block}

/* top bar */
.topbar{height:32px;position:relative}
.topbar .band{position:absolute;left:605px;right:0;top:0;height:32px;background:var(--teal)}
.topnav{position:absolute;left:615px;top:0;display:flex;height:32px;font-size:11px;font-weight:600;text-transform:uppercase}
.topnav a{padding:0 22px;line-height:32px;color:var(--ink)}
.topnav a.active{background:var(--white)}
.topnav .phone{display:flex;align-items:center;gap:6px;font-size:15px;padding-left:14px}

/* header */
.header{height:115px;display:flex;align-items:center;justify-content:space-between;padding:0 131px}
.brand{display:flex;align-items:center;gap:12px}
.brand .dot{width:44px;height:44px;border-radius:50%;background:var(--teal)}
.brand .name{font-size:30px;font-weight:400;color:var(--teal-dark)}
.brand .tag{font-size:12px;color:var(--teal-dark);display:block;margin-top:-2px}
.header-tools{display:flex;gap:26px}
.search{width:300px;height:46px;border:1px solid var(--line);display:flex;align-items:center;padding:0 16px;gap:10px;font-size:11px;color:var(--muted)}
.cart{width:130px;height:46px;border:1px solid var(--line);display:flex;align-items:center;padding:0 14px;gap:10px;font-size:10px;color:var(--muted)}
.cart b{color:var(--red);display:block}

/* main nav */
.mainnav{height:57px;border-top:1px solid var(--line);border-bottom:1px solid var(--line)}
.mainnav ul{list-style:none;display:flex;justify-content:space-between;align-items:center;height:100%;width:940px;margin:0 auto;font-size:11px;font-weight:600;text-transform:uppercase}
.mainnav li{display:flex;align-items:center;gap:8px;line-height:1.2}

/* hero */
.hero{height:488px;margin-top:5px;position:relative;background:linear-gradient(100deg,#cfe6ef 0%,#b9dbe9 40%,#9ac9dc 100%)}
.hero .people{position:absolute;left:480px;top:0;width:720px;height:488px;background:linear-gradient(120deg,#d9b08d 0%,#c78a66 45%,#8fb9cf 100%)}
.hero h1{position:absolute;left:156px;top:158px;color:var(--red);font-size:42px;font-weight:700;line-height:1.2;text-transform:uppercase}
.hero .outline{position:absolute;left:162px;top:280px;border:2px solid var(--red);color:var(--red);font-size:15px;font-weight:600;padding:6px 14px;text-transform:uppercase}
.dots{position:absolute;left:528px;bottom:10px;background:rgba(0,0,0,.45);display:flex;gap:16px;padding:7px 12px}
.dots i{width:9px;height:9px;border-radius:50%;background:var(--white);display:block}
.dots i.on{background:transparent;border:2px solid var(--white)}

/* services */
.services{height:371px;padding-top:32px}
.services .grid{display:flex;justify-content:space-between;width:1012px;margin:0 auto}
.svc{width:245px;text-align:center}
.svc .photo{height:201px}
.svc h3{color:var(--red);font-size:14px;font-weight:700;text-transform:uppercase;margin:18px 0 12px;line-height:1.35}

/* psychologists */
.psych{height:416px;background:var(--grey-bg);padding-top:52px}
.psych .section-title{font-size:19px}
.psych p{margin-top:20px;line-height:1.75;color:var(--muted);font-size:12.5px}
.psych .cols{display:flex;margin-top:40px}
.psych ul{list-style:none;width:340px;padding-left:60px}
.psych li{font-size:12.5px;color:var(--muted);line-height:28px;display:flex;align-items:center;gap:14px}
.psych li::before{content:"";width:6px;height:6px;border-right:1.5px solid var(--teal-dark);border-top:1.5px solid var(--teal-dark);transform:rotate(45deg)}

/* specialise */
.special{height:469px;padding-top:53px}
.special .wrap{display:flex;gap:48px}
.video{width:534px;height:356px;position:relative;background:linear-gradient(135deg,#4a3a35,#8a6d5e 60%,#b59a86)}
.video svg{position:absolute;left:224px;top:135px}
.special .text{width:360px;padding-top:2px}
.special h2{color:var(--red);font-size:22px;font-weight:400;text-transform:uppercase;line-height:1.3}
.special p{margin-top:22px;color:var(--muted);font-size:12.5px;line-height:1.85}
.special .btn{margin-top:26px}

/* blog */
.blog{height:570px;background:var(--grey-bg);padding-top:50px}
.arrows{position:absolute;right:0;top:4px;display:flex;gap:14px}
.blog .cards{display:flex;justify-content:space-between;margin-top:30px}
.post{width:298px;height:396px;background:var(--white);position:relative}
.post .photo{height:196px}
.post .date{position:absolute;left:26px;top:186px;background:var(--white);font-size:9px;padding:3px 8px}
.post h3{font-size:15.5px;font-weight:400;line-height:1.55;padding:24px 20px 0 24px;letter-spacing:-.1px;height:82px}
.post p{font-size:12px;color:var(--muted);line-height:1.6;padding:10px 24px 0}
.post .btn{margin:22px 24px 0}

/* topic tiles */
.tiles{height:525px;padding-top:46px}
.tiles .grid{display:grid;grid-template-columns:repeat(3,299px);gap:18px 21px}
.tile{height:204px;position:relative}
.tile span{position:absolute;left:16px;bottom:12px;color:var(--white);font-size:15px;font-weight:600;line-height:1.3;width:165px}
.tile .btn{position:absolute;right:10px;bottom:10px;font-size:10px}

/* gallery */
.gallery{height:357px;background:var(--grey-bg);padding-top:55px}
.gallery .row{display:flex;justify-content:space-between;margin-top:32px}
.gallery .photo{width:226px;height:166px}

/* rebates */
.rebates{height:228px;padding-top:58px;text-align:center;border-bottom:1px solid var(--line)}
.rebates .badges{display:flex;justify-content:center;align-items:center;gap:22px;margin-top:40px}
.badge{height:26px;border-radius:4px}

/* footer */
.footer{height:268px;padding-top:60px}
.footer .wrap{display:flex}
.footer .brand{width:380px;align-items:flex-start}
.fcol{width:145px}
.fcol.wide{width:235px}
.fcol.last{width:180px}
.fcol h4{color:var(--red);font-size:11px;font-weight:700;text-transform:uppercase;margin-bottom:12px}
.fcol a{display:block;font-size:11px;line-height:20px;color:var(--ink);white-space:nowrap}
.bottom{height:105px;border-top:1px solid var(--line)}
.bottom .wrap{display:flex;justify-content:space-between;align-items:center;height:100%}
.follow{display:flex;align-items:center;gap:8px;font-size:11px;font-weight:700;color:var(--red);text-transform:uppercase}
.follow i{width:24px;height:24px;border-radius:50%;display:block}
.copy{font-size:10px;color:var(--muted)}
</style>
</head>
<body>

<div class="topbar">
  <div class="band"></div>
  <nav class="topnav">
    <a class="active" href="#">Home</a>
    <a href="#">About us</a>
    <a href="#">FAQ</a>
    <a href="#">Contact</a>
    <a class="phone" href="#"><svg width="14" height="14" viewBox="0 0 24 24"><path d="M6.6 10.8a15 15 0 0 0 6.6 6.6l2.2-2.2c.3-.3.7-.4 1-.2 1.1.4 2.3.6 3.6.6.6 0 1 .4 1 1V20c0 .6-.4 1-1 1A17 17 0 0 1 3 4c0-.6.4-1 1-1h3.5c.6 0 1 .4 1 1 0 1.3.2 2.5.6 3.6.1.3 0 .7-.2 1z" fill="#333"/></svg>1300 555 214</a>
  </nav>
</div>

<header class="header">
  <div class="brand">
    <span class="dot"></span>
    <div><span class="name">The Kelvale Clinic</span><span class="tag">helping you create loving relationships</span></div>
  </div>
  <div class="header-tools">
    <div class="search"><svg width="12" height="12" viewBox="0 0 24 24"><circle cx="10" cy="10" r="7" stroke="#333" stroke-width="3" fill="none"/><path d="M15 15l7 7" stroke="#333" stroke-width="3"/></svg>SEARCH</div>
    <div class="cart"><svg width="18" height="16" viewBox="0 0 24 22"><path d="M1 2h4l3 12h12l3-9H7" stroke="#333" stroke-width="2" fill="none"/><circle cx="10" cy="19" r="2" fill="#333"/><circle cx="18" cy="19" r="2" fill="#333"/></svg><div>MY CART (0)<b>$0.00</b></div></div>
  </div>
</header>

<nav class="mainnav">
  <ul>
    <li>Counselling<br>Types <svg width="10" height="6"><path d="M1 1l4 4 4-4" stroke="#333" fill="none"/></svg></li>
    <li>Relationship Counselling<br>Locations <svg width="10" height="6"><path d="M1 1l4 4 4-4" stroke="#333" fill="none"/></svg></li>
    <li>Sex Therapy<br>Locations <svg width="10" height="6"><path d="M1 1l4 4 4-4" stroke="#333" fill="none"/></svg></li>
    <li>Quizzes</li>
    <li>Resources</li>
    <li>Blog</li>
  </ul>
</nav>

<section class="hero">
  <div class="people" role="img" aria-label="Smiling couple outdoors, woman riding on man's back against a blue sky"></div>
  <h1>Relationship<br>Counselling</h1>
  <a class="outline" href="#">Read more</a>
  <div class="dots"><i></i><i class="on"></i><i></i><i></i><i></i></div>
</section>

<section class="services">
  <div class="grid">
    <div class="svc"><div class="photo" role="img" aria-label="Couple sitting apart on a sofa" style="background:linear-gradient(135deg,#cfd8dc,#8e9ea6)"></div><h3>Relationship<br>Counselling</h3><a class="btn" href="#">Read more</a></div>
    <div class="svc"><div class="photo" role="img" aria-label="Couple sitting on a bed" style="background:linear-gradient(135deg,#efe6dc,#bba58f)"></div><h3>Sex Therapy<br>Counselling</h3><a class="btn" href="#">Read more</a></div>
    <div class="svc"><div class="photo" role="img" aria-label="Man in a shirt looking calm" style="background:linear-gradient(135deg,#e7e9ec,#a9b2bb)"></div><h3>Anger Management<br>Counselling</h3><a class="btn" href="#">Read more</a></div>
    <div class="svc"><div class="photo" role="img" aria-label="Couple in a tense moment" style="background:linear-gradient(135deg,#8fa3b8,#b07a65)"></div><h3>Narcissism<br>Counselling</h3><a class="btn" href="#">Read more</a></div>
  </div>
</section>

<section class="psych">
  <div class="wrap">
    <h2 class="section-title">Our Kelvale Relationship Psychologists</h2>
    <p>Our team of 75 hand chosen Registered Psychologists in 81 locations Australia wide, are individually selected for their knowledge, experience, compassion, and unbiased approach to marriage counselling and sexual therapy.</p>
    <div class="cols">
      <ul><li>Affairs</li><li>Controlling behaviour</li><li>Verbal abuse</li><li>Imbalance of power</li><li>Lack of intimacy</li><li>Poor communication</li></ul>
      <ul><li>Loss of love</li><li>Relationship neglect</li><li>Sexual problems</li><li>Problems from childhood</li><li>Problems with parenting your children</li><li>Step children and in-laws</li></ul>
      <ul><li>All forms of family problems</li><li>Anger management problems</li><li>Porn addiction problems</li><li>Pre-marriage programs</li><li>Narcissism problems</li></ul>
    </div>
  </div>
</section>

<section class="special">
  <div class="wrap">
    <div class="video" role="img" aria-label="Video still of a psychologist speaking in her office">
      <svg width="80" height="80" viewBox="0 0 80 80"><circle cx="40" cy="40" r="40" fill="#ec1f27"/><path d="M32 24l24 16-24 16z" fill="#fff"/></svg>
    </div>
    <div class="text">
      <h2>We specialise in relationship<br>&amp; marriage counselling</h2>
      <p>At the Kelvale Clinic, we are a group of PSYCHOLOGISTS, Australia wide who are passionate about relationships and helping you with yours.</p>
      <p>Our vision is to provide the most highly regarded and comprehensive marriage counselling and relationship counselling, and sex therapy in Australia, at reasonable and affordable rates.</p>
      <a class="btn" href="#">Read more</a>
    </div>
  </div>
</section>

<section class="blog">
  <div class="wrap">
    <h2 class="section-title">Latest Blog</h2>
    <div class="arrows"><svg width="14" height="22"><path d="M12 2L3 11l9 9" stroke="#333" stroke-width="2.5" fill="none"/></svg><svg width="14" height="22"><path d="M2 2l9 9-9 9" stroke="#333" stroke-width="2.5" fill="none"/></svg></div>
    <div class="cards">
      <article class="post"><div class="photo" role="img" aria-label="Woman raising a finger to her lips" style="background:linear-gradient(135deg,#6d3e3a,#c49585)"></div><span class="date">April 15,2017</span><h3>Are You Living With a<br>Steamroller?</h3><p>It is a long established fact that a re ader will be distracted by the readable</p><a class="btn" href="#">Read more</a></article>
      <article class="post"><div class="photo" role="img" aria-label="Upset woman sitting on a sofa" style="background:linear-gradient(135deg,#b8a392,#6e5a4d)"></div><span class="date">April 15,2017</span><h3>How Do I Know If I'm With a<br>Narcissist?</h3><p>It is a long established fact that a re ader will be distracted by the readable</p><a class="btn" href="#">Read more</a></article>
      <article class="post"><div class="photo" role="img" aria-label="Couple talking at a table" style="background:linear-gradient(135deg,#d9dde2,#7d8ea3)"></div><span class="date">April 15,2017</span><h3>Letter for a Partner Doubtful<br>About Relationship Counselling</h3><p>It is a long established fact that a re ader will be distracted by the readable</p><a class="btn" href="#">Read more</a></article>
    </div>
  </div>
</section>

<section class="tiles">
  <div class="wrap grid">
    <div class="tile" role="img" aria-label="Couple in a dim setting" style="background:linear-gradient(135deg,#6b6a3a,#2d2a1a)"><span>How to deal with<br>an affair</span><a class="btn" href="#">Read more</a></div>
    <div class="tile" role="img" aria-label="Two hands holding together" style="background:linear-gradient(135deg,#7a5040,#3a2a25)"><span>Same Sex Relationships &amp; Counselling</span><a class="btn" href="#">Read more</a></div>
    <div class="tile" role="img" aria-label="Man in a suit" style="background:linear-gradient(135deg,#e4e4e4,#5a5a5a)"><span>Are you living with a narcissist</span><a class="btn" href="#">Read more</a></div>
    <div class="tile" role="img" aria-label="Couple turned away from each other" style="background:linear-gradient(135deg,#6a5a52,#2a2220)"><span>Is one of you an Intimacy Withholder</span><a class="btn" href="#">Read more</a></div>
    <div class="tile" role="img" aria-label="Man at a laptop at night" style="background:linear-gradient(135deg,#4e4a44,#1e1c1a)"><span>Is too much porn affecting your relationship?</span><a class="btn" href="#">Read more</a></div>
    <div class="tile" role="img" aria-label="Distressed woman sitting alone" style="background:linear-gradient(135deg,#9c8470,#3e342c)"><span>Is your relationship safe? Is your partner controlling?</span><a class="btn" href="#">Read more</a></div>
  </div>
</section>

<section class="gallery">
  <div class="wrap">
    <h2 class="section-title">Photo Gallery</h2>
    <div class="arrows"><svg width="14" height="22"><path d="M12 2L3 11l9 9" stroke="#333" stroke-width="2.5" fill="none"/></svg><svg width="14" height="22"><path d="M2 2l9 9-9 9" stroke="#333" stroke-width="2.5" fill="none"/></svg></div>
    <div class="row">
      <div class="photo" role="img" aria-label="Couple with red heart balloons" style="background:linear-gradient(135deg,#f1e3dc,#d64a4a)"></div>
      <div class="photo" role="img" aria-label="Couple in a hotel room" style="background:linear-gradient(135deg,#8a6a55,#e1cdb8)"></div>
      <div class="photo" role="img" aria-label="Couple arm wrestling" style="background:linear-gradient(135deg,#c9b89a,#c45a3a)"></div>
      <div class="photo" role="img" aria-label="Couple sitting apart on a bed" style="background:linear-gradient(135deg,#f0f0f0,#9a9a9a)"></div>
    </div>
  </div>
</section>

<section class="rebates">
  <h2 class="section-title">Rebates Available</h2>
  <div class="badges">
    <span class="badge" style="width:110px;background:#3b9a45"></span>
    <span class="badge" style="width:96px;background:#1a7bc4"></span>
    <span class="badge" style="width:110px;background:#8a8a8a"></span>
    <span class="badge" style="width:96px;background:#5aa846"></span>
    <span class="badge" style="width:30px;background:#2e9bd6"></span>
    <span class="badge" style="width:40px;background:#7cc3a8"></span>
    <span class="badge" style="width:46px;background:#d8342e"></span>
    <span class="badge" style="width:22px;background:#1f6fbf"></span>
    <span class="badge" style="width:30px;border-radius:50%;background:#2c3b6b"></span>
  </div>
</section>

<footer class="footer">
  <div class="wrap">
    <div class="brand">
      <span class="dot"></span>
      <div><span class="name">The Kelvale Clinic</span><span class="tag">helping you create loving relationships</span></div>
    </div>
    <div class="fcol"><h4>Menu</h4><a href="#">Home</a><a href="#">About</a><a href="#">Resources</a><a href="#">Blog</a><a href="#">FAQs</a><a href="#">Contact</a></div>
    <div class="fcol wide"><h4>Services</h4><a href="#">Join our Associate Program</a><a href="#">Marriage Counselling</a><a href="#">Relationship Counselling</a></div>
    <div class="fcol last"><h4>Links</h4><a href="#">Privacy Policy</a><a href="#">Terms &amp; Conditions</a><a href="#">Site Map</a><a href="#">Associate Psychologists Program</a><a href="#">Contact Us</a></div>
  </div>
</footer>

<div class="bottom">
  <div class="wrap">
    <div class="follow">Follow us
      <i style="background:#3b5998;margin-left:8px"></i><i style="background:#1da1f2"></i><i style="background:#dd4b39"></i><i style="background:#cc181e"></i>
    </div>
    <div class="copy">Copyrights © 2017 All Rights Reserved</div>
  </div>
</div>

</body>
</html>
```